Bramblewick Forage Business Cards

I need a business card with my logo, number, Facebook account, and some information about what I am selling. Green card with logo on the front. 555-214-8392 phone number, @bramblewickforage Facebook, •Orchardgrass Hay •Alfalfa Hay •Mixed Grass Hay , and “Premium Quality Hay” all written on the back.

Target Market(s)

Hay

Contact Information for Business Card

Phone number, Facebook, different types of hay.

Colors
00AB8E
00BBA5
67D7C9
C6EFE9
E9F9F6

```html
<!DOCTYPE html>
<html lang="en">
<head>
<meta charset="utf-8">
<title>Bramblewick Forage Business Cards</title>
<link rel="stylesheet" href="https://fonts.googleapis.com/css2?family=Roboto:ital,wght@0,400;0,500;0,700;1,400&display=swap">
<style>
  :root {
    --canvas: #e6e6e6;
    --card-white: #ffffff;
    --ink: #2b2b2b;
    --black: #0d0d0d;
    --green: #00a65a;
    --dark-top: #2c2c2e;
    --dark-bottom: #111112;
    --light-text: #ffffff;
  }
  * { margin: 0; padding: 0; box-sizing: border-box; }
  html, body {
    width: 1200px; height: 1200px; overflow: hidden;
    background: var(--canvas);
    font-family: "Roboto", Arial, sans-serif;
  }
  .card {
    position: absolute;
    left: 257px;
    width: 686px; height: 392px;
    border-radius: 24px;
    overflow: hidden;
  }
  .card--front { top: 165px; background: var(--card-white); }
  .card--back {
    top: 653px;
    background: linear-gradient(160deg, var(--dark-top), var(--dark-bottom) 60%);
  }

  /* front */
  .brand-mark {
    position: absolute; left: 128px; top: 136px;
    width: 100px; height: 100px; border-radius: 50%;
    background: var(--green);
  }
  .brand-name {
    position: absolute; left: 252px; top: 140px;
    font-weight: 500; font-size: 36px; color: var(--ink);
    white-space: nowrap;
  }
  .phone {
    position: absolute; left: 268px; top: 196px;
    font-weight: 700; font-size: 42px; color: var(--ink);
    letter-spacing: 0.5px;
  }
  .front-bands { position: absolute; left: 0; top: 0; }
  .social {
    position: absolute; left: 486px; top: 352px;
    display: flex; align-items: center; gap: 7px;
    color: var(--light-text); font-style: italic; font-size: 17px;
  }
  .social__dot {
    width: 20px; height: 20px; border-radius: 50%;
    background: var(--light-text);
  }

  /* back */
  .back-decoration {
    position: absolute; left: 300px; top: 60px;
    width: 360px; height: 360px; border-radius: 50%;
    background: var(--green);
  }
  .back-name {
    position: absolute; left: 52px; top: 52px;
    font-weight: 500; font-size: 36px; color: var(--light-text);
    white-space: nowrap;
  }
  .products {
    position: absolute; left: 50px; top: 112px;
    list-style: none; color: var(--light-text); font-size: 15.5px; line-height: 20px;
  }
  .products li { display: flex; gap: 10px; }
  .products span::before {
    content: ""; display: inline-block;
    width: 6px; height: 6px; border-radius: 50%;
    background: var(--green);
    margin-right: 7px; vertical-align: middle; position: relative; top: -1px;
  }
</style>
</head>
<body>
  <section class="card card--front">
    <div class="brand-mark" aria-hidden="true"></div>
    <div class="brand-name">Bramblewick Forage</div>
    <div class="phone">555-214-8392</div>
    <svg class="front-bands" width="686" height="392" viewBox="0 0 686 392" aria-hidden="true">
      <path d="M0,363 H450 C440,370 433,374 422,374 H0 Z" fill="var(--black)"/>
      <path d="M0,381 H440 C470,381 482,340 522,340 H686 V392 H0 Z" fill="var(--green)"/>
    </svg>
    <div class="social"><span class="social__dot" aria-hidden="true"></span>@bramblewickforage</div>
  </section>

  <section class="card card--back">
    <div class="back-decoration" aria-hidden="true"></div>
    <div class="back-name">Bramblewick Forage</div>
    <ul class="products">
      <li><span>Orchardgrass Hay</span><span>Alfalfa Hay</span></li>
      <li><span>Mixed Grass Hay &amp; Premium Quality Hay</span></li>
    </ul>
  </section>
</body>
</html>
```